Construction Company

Design a clutter free business card, it can be double-sided utilizing the logo for VKM Ltd simple with all relevant contact information.

Please also a letterhead design to function for the purposes of invoicing, all mail requirements, with header to be distinctive while the footer ties page together and incorporates all necessary information.

For now, please use generic / dummy text and when a winner is selected, I will disclose the contact information.

Hi Designers! Please read the updated brief which includes the design of a business card and letterhead. Thank you!

```html
<!DOCTYPE html>
<html lang="en">
<head>
<meta charset="utf-8">
<title>VKM Ltd – Business Card</title>
<link href="https://fonts.googleapis.com/css2?family=Cinzel:wght@600&family=Jost:wght@400&family=Roboto:wght@400&display=swap" rel="stylesheet">
<style>
  :root {
    --navy: #00308f;
    --gold: #b38b00;
    --ink: #3a3a3a;
    --paper: #ffffff;
    --backdrop: #e6e6e6;
  }
  * { margin: 0; padding: 0; box-sizing: border-box; }
  html, body { width: 1200px; height: 1200px; overflow: hidden; }
  body { background: var(--backdrop); position: relative; font-family: "Jost", sans-serif; }

  .card {
    position: absolute;
    left: 262px;
    width: 686px;
    height: 392px;
    border-radius: 26px;
    overflow: hidden;
  }
  .card--front { top: 165px; background: var(--paper); }
  .card--back { top: 653px; background: var(--navy); }

  .brand-name {
    position: absolute;
    left: 74px;
    top: 160px;
    width: 264px;
    text-align: center;
    font-family: "Cinzel", serif;
    font-weight: 600;
    font-size: 50px;
    line-height: 70px;
    color: var(--navy);
    letter-spacing: 1px;
  }

  .divider {
    position: absolute;
    left: 367px;
    top: 88px;
    width: 1px;
    height: 214px;
    background: #555;
  }

  .details { position: absolute; left: 394px; top: 90px; color: var(--ink); }
  .details__name {
    font-family: "Cinzel", serif;
    font-weight: 600;
    font-size: 26px;
    line-height: 30px;
    color: var(--navy);
    letter-spacing: 0.5px;
  }
  .details__role { font-size: 16px; line-height: 20px; color: var(--gold); }
  .details__address { margin-top: 14px; font-size: 15.5px; line-height: 19px; letter-spacing: 0.3px; }
  .contact-list { list-style: none; margin-top: 14px; }
  .contact-list li {
    display: flex;
    align-items: center;
    font-size: 15.5px;
    line-height: 19.5px;
    letter-spacing: 0.3px;
  }
  .contact-list svg { width: 13px; height: 13px; margin-right: 10px; fill: var(--navy); flex: none; }

  .edge-band { position: absolute; left: 0; bottom: 0; width: 686px; height: 16px; }

  .back-mark {
    position: absolute;
    left: 0; right: 0;
    top: 160px;
    text-align: center;
    font-family: "Cinzel", serif;
    font-weight: 600;
    font-size: 54px;
    line-height: 70px;
    color: var(--gold);
    letter-spacing: 2px;
  }
  .back-web {
    position: absolute;
    left: 0; right: 0;
    top: 341px;
    text-align: center;
    font-family: "Roboto", sans-serif;
    font-size: 16px;
    letter-spacing: 4.6px;
    color: #ffffff;
  }
</style>
</head>
<body>
  <section class="card card--front">
    <div class="brand-name">VKM Ltd</div>
    <div class="divider"></div>
    <div class="details">
      <div class="details__name">DANIEL ROURKE</div>
      <div class="details__role">President</div>
      <div class="details__address">4120 Alder Creek Road<br>Juneau, Alaska 34610</div>
      <ul class="contact-list">
        <li><svg viewBox="0 0 16 16"><path d="M3.5 1 6 3.5 4.8 5.6c.9 2 3 4.2 5.6 5.6L12.5 10 15 12.5 13.4 15C7 14.6 1.4 9 1 2.6z"/></svg>555-214-7730</li>
        <li><svg viewBox="0 0 16 16"><path d="M4 0h8v16H4zM5.5 2v10h5V2zM7 13.2v1.3h2v-1.3z"/></svg>555-608-1942</li>
        <li><svg viewBox="0 0 16 16"><path d="M4 1h8v5H4zM1 7h14v6H1zM3 14h10v1H3z"/></svg>555-377-4186</li>
        <li><svg viewBox="0 0 16 16"><path d="M1 4h14v9H1zM2.2 5 8 9.3 13.8 5H12L8 8 4 5z"/></svg>info@vkmltd.com</li>
        <li><svg viewBox="0 0 16 16"><path d="M8 1a7 7 0 1 0 0 14A7 7 0 0 0 8 1zm-1 2.3c-.6 1-2 1.2-2 2.7 1.2.4 2.6.1 3 1.5-.4 1.6-1.6 1.4-1.5 3 0 .7.5 1.5.3 2.2A5 5 0 0 1 7 3.3zm3 .2a5 5 0 0 1 2.8 5.6c-1-.4-1.5-1.6-2.8-1.3-.8-.8.6-1.7 0-2.6z"/></svg>www.vkmltd.com</li>
      </ul>
    </div>
    <svg class="edge-band" viewBox="0 0 686 16" preserveAspectRatio="none">
      <polygon points="0,0 449,0 444,16 0,16" fill="var(--navy)"/>
      <polygon points="452,0 686,0 686,16 447,16" fill="var(--gold)"/>
    </svg>
  </section>

  <section class="card card--back">
    <div class="back-mark">VKM LTD</div>
    <div class="back-web">WWW.VKMLTD.COM</div>
  </section>
</body>
</html>
```